Design some Business Card for shipping company

We need a creative business card designed for a shipping company. All relevant information such as address and phone number can be found on our website. Will need a design for both front and back. The front will container our logo, slogan, contact information etc. The back will have a coupon and some text. check out www.larvintolfreight.example for all the information. We need something memorable and unique that will stand out. It needs to a horizontal design. Not vertical.

```html
<!DOCTYPE html>
<html lang="en">
<head>
<meta charset="utf-8">
<title>Larvintol Freight – Business Card</title>
<link rel="stylesheet" href="https://fonts.googleapis.com/css2?family=Montserrat:wght@500;600;700;800&display=swap">
<style>
  :root {
    --bg: #2a2a2a;
    --card: #ffffff;
    --green: #237a45;
    --red: #c9363e;
    --black: #111111;
    --ink: #1d1d1d;
    --muted: #333333;
  }
  * { margin: 0; padding: 0; box-sizing: border-box; }
  html, body { width: 1200px; height: 780px; overflow: hidden; }
  body {
    background: var(--bg);
    font-family: "Montserrat", Arial, sans-serif;
    position: relative;
  }
  .card {
    position: absolute;
    width: 560px;
    height: 320px;
    background: var(--card);
    overflow: hidden;
    box-shadow: 0 10px 24px rgba(0,0,0,.45);
  }
  .card--front { left: 25px; top: 230px; }
  .card--back { left: 615px; top: 230px; }
  .card__bands { position: absolute; left: 0; top: 0; width: 560px; height: 320px; }

  /* Front */
  .front-brand {
    position: absolute; left: 0; right: 0; top: 48px;
    display: flex; flex-direction: column; align-items: center;
  }
  .brand-dot {
    width: 74px; height: 74px; border-radius: 50%;
    background: var(--green);
  }
  .front-brand__name {
    margin-top: 18px;
    font-size: 38px; font-weight: 700; letter-spacing: .5px;
    color: var(--green); text-transform: uppercase;
  }
  .front-brand__slogan {
    margin-top: 4px;
    font-size: 17px; font-weight: 800; color: var(--ink);
  }
  .front-url {
    position: absolute; left: 214px; width: 256px; top: 282px;
    font-size: 12px; font-weight: 700; color: #fff; text-align: center;
  }

  /* Back */
  .back-brand {
    position: absolute; left: 26px; top: 124px;
    display: flex; align-items: center; gap: 10px;
  }
  .back-brand .brand-dot { width: 40px; height: 40px; }
  .back-brand__name {
    font-size: 19px; font-weight: 700; color: var(--green); text-transform: uppercase;
  }
  .back-brand__slogan { font-size: 9.5px; font-weight: 800; color: var(--ink); }
  .coupon-lines { position: absolute; left: 40px; top: 172px; width: 235px; }
  .coupon-lines span { display: block; height: 2px; background: var(--red); margin-bottom: 21px; }

  .person { position: absolute; right: 30px; top: 40px; text-align: right; }
  .person__name { font-size: 29px; font-weight: 600; color: var(--ink); }
  .person__role { font-size: 14px; font-weight: 600; color: var(--muted); margin-top: 2px; }

  .contact-list {
    position: absolute; right: 22px; top: 118px; list-style: none;
    font-size: 10px; font-weight: 600; color: var(--muted); text-align: right;
  }
  .contact-list li { display: flex; align-items: center; justify-content: flex-end; gap: 8px; height: 20px; }
  .contact-list svg { width: 16px; height: 16px; flex: none; }
  .contact-list .no-icon { padding-right: 24px; }
</style>
</head>
<body>

<section class="card card--front" aria-label="Business card front">
  <div class="front-brand">
    <div class="brand-dot"></div>
    <div class="front-brand__name">Larvintol Freight</div>
    <div class="front-brand__slogan">Secure Affordable Shipping to Kenya</div>
  </div>
  <svg class="card__bands" viewBox="0 0 560 320" aria-hidden="true">
    <polygon points="0,298 220,298 206,320 0,320" fill="var(--black)"/>
    <polygon points="228,276 470,276 452,302 210,302" fill="var(--red)"/>
    <polygon points="470,276 560,258 560,280 452,302" fill="var(--green)"/>
  </svg>
  <div class="front-url">www.larvintolfreight.example</div>
</section>

<section class="card card--back" aria-label="Business card back">
  <div class="person">
    <div class="person__name">Amani Wekesa</div>
    <div class="person__role">Director</div>
  </div>

  <div class="back-brand">
    <div class="brand-dot"></div>
    <div>
      <div class="back-brand__name">Larvintol Freight</div>
      <div class="back-brand__slogan">Secure Affordable Shipping to Kenya</div>
    </div>
  </div>
  <div class="coupon-lines"><span></span><span></span><span></span><span></span></div>

  <ul class="contact-list">
    <li>USA: +1 555 014 2290
      <svg viewBox="0 0 16 16"><rect x="1" y="1" width="14" height="14" rx="3" fill="var(--red)"/><rect x="5.5" y="3.5" width="5" height="9" rx="1" fill="none" stroke="#fff" stroke-width="1.3"/></svg></li>
    <li>KENYA: +254700000123, 0700000123
      <svg viewBox="0 0 16 16"><rect x="1" y="1" width="14" height="14" rx="3" fill="var(--red)"/><rect x="5.5" y="3.5" width="5" height="9" rx="1" fill="none" stroke="#fff" stroke-width="1.3"/></svg></li>
    <li>info@larvintolfreight.example
      <svg viewBox="0 0 16 16"><rect x="1" y="1" width="14" height="14" rx="3" fill="var(--red)"/><rect x="3.5" y="5" width="9" height="6.5" fill="none" stroke="#fff" stroke-width="1.2"/><polyline points="3.5,5 8,8.6 12.5,5" fill="none" stroke="#fff" stroke-width="1.2"/></svg></li>
    <li>www.larvintolfreight.example
      <svg viewBox="0 0 16 16"><circle cx="8" cy="8" r="7" fill="var(--red)"/><circle cx="8" cy="8" r="4.6" fill="none" stroke="#fff" stroke-width="1"/><ellipse cx="8" cy="8" rx="2" ry="4.6" fill="none" stroke="#fff" stroke-width="1"/><line x1="3.4" y1="8" x2="12.6" y2="8" stroke="#fff" stroke-width="1"/></svg></li>
    <li>418 Harbor Point Ave Ste #12
      <svg viewBox="0 0 16 16"><polygon points="8,2 15,8 13,8 13,14 3,14 3,8 1,8" fill="var(--red)"/><rect x="6.5" y="10" width="3" height="4" fill="#fff"/></svg></li>
    <li class="no-icon">Fairview WA 98000</li>
  </ul>

  <svg class="card__bands" viewBox="0 0 560 320" aria-hidden="true">
    <polygon points="0,292 150,300 136,320 0,320" fill="var(--black)"/>
    <polygon points="150,300 410,286 392,306 136,320" fill="var(--red)"/>
    <polygon points="420,284 560,278 560,298 402,306" fill="var(--green)"/>
  </svg>
</section>

</body>
</html>
```